Travel Agency Website - Simple General

Need a 7 page simple design that is pretty repetitive. Need to be able to load quickly that is SEO optimized. Trying to give ideas on what they can do, be personal as we are local, but at the same time come across as professional and get information easily with little burden.

- Landing Page
- Brimwell Vacations Page
- Family Trips
- Road Trips from Texas
- Other Destinations
- About Us Page
- Contact Us Page

Target Market(s)

Families

Coding

Coded - Design and coding required

Number of Pages Required

5+ page

Colors

Designer to choose colors to be used in the design.

Requirements
Must have
• Like it to flow easily with our logo. Use that for colors, etc.

```html
<!DOCTYPE html>
<html lang="en">
<head>
<meta charset="utf-8">
<title>Roamwell Travel Co. — Let's Explore The World</title>
<link href="https://fonts.googleapis.com/css2?family=Outfit:wght@300;400;500;600;700&display=swap" rel="stylesheet">
<style>
:root{
  --ink:#121212;
  --paper:#ffffff;
  --teal:#2f7a6e;
  --teal-soft:#e5f0ed;
  --muted:#555a58;
  --line:#e6e6e6;
  --footer:#1b1a19;
}
*{box-sizing:border-box;margin:0;padding:0}
html,body{width:1200px;height:4032px;overflow:hidden}
body{font-family:'Outfit',sans-serif;color:var(--ink);background:var(--paper);position:relative}
.abs{position:absolute}
.photo{position:absolute;overflow:hidden}
a{color:inherit;text-decoration:none}

/* hero */
.hero{left:40px;top:34px;width:1120px;height:716px;border-radius:22px;overflow:hidden;
  background:linear-gradient(180deg,#2b2a22 0%,#4a4530 30%,#6d6440 55%,#3b3524 80%,#1f1d16 100%)}
.hero::after{content:"";position:absolute;inset:0;background:linear-gradient(90deg,rgba(0,0,0,.45),rgba(0,0,0,0) 65%)}
.hero>*{z-index:1}
.brand{display:flex;align-items:center;gap:10px;font-weight:600;font-size:20px}
.brand-dot{width:34px;height:34px;border-radius:50%;background:#f3ecdc}
.nav{left:234px;top:55px;height:42px;width:651px;border:1px solid rgba(255,255,255,.45);border-radius:22px;
  background:rgba(255,255,255,.08);display:flex;align-items:center;justify-content:space-around;padding:0 10px;color:#fff;font-size:14px}
.btn{display:flex;align-items:center;height:42px;padding:0 20px;border-radius:21px;background:var(--ink);color:#fff;font-size:14px}
.arrow{width:40px;height:40px;border-radius:50%;background:var(--ink);display:flex;align-items:center;justify-content:center}
.hero h1{left:36px;top:210px;color:#fff;font-weight:700;font-size:70px;line-height:80px;letter-spacing:-.5px}
.hero-pill{left:220px;top:216px;width:278px;height:70px;border-radius:35px;background:linear-gradient(90deg,#c9d6d8,#b89c7c 50%,#6d8792)}
.hero-copy{left:36px;top:394px;width:470px;color:#e8e4da;font-size:12.5px;line-height:21px;font-weight:300}
.stats{left:36px;top:476px;display:flex;gap:40px;color:#fff}
.stat b{font-weight:500;font-size:34px;display:flex;align-items:center;gap:8px}
.stat span{display:block;font-size:12.5px;color:#d9d5ca;font-weight:300;margin:10px 0 0 24px}
.side{left:1040px;top:542px;width:44px;height:136px;border-radius:22px;background:rgba(255,255,255,.25);
  display:flex;flex-direction:column;align-items:center;justify-content:space-around;padding:10px 0}
.side i{width:16px;height:16px;border-radius:4px;background:#fff;display:block}

/* section heads */
.eyebrow{display:flex;align-items:center;gap:10px;color:var(--teal);font-size:13px;letter-spacing:2.2px;font-weight:500}
.title{font-size:40px;font-weight:500;letter-spacing:-.3px}
.lede{font-size:12.5px;line-height:21px;color:var(--muted);font-weight:300}
.lede b{color:var(--ink);font-weight:500}

.card{border-radius:16px}
.rating{left:14px;top:14px;height:26px;padding:0 10px;border-radius:13px;background:rgba(255,255,255,.35);
  color:#fff;font-size:13px;display:flex;align-items:center;gap:6px}

.para{font-size:12.5px;line-height:25px;color:var(--muted);font-weight:300;margin-bottom:8px}

/* difference stats */
.statbar{left:84px;top:2531px;width:1027px;height:110px;border-radius:16px;background:#fff;display:flex;align-items:center;
  box-shadow:0 8px 30px rgba(0,0,0,.08)}
.dstat{position:absolute;display:flex;align-items:center;gap:14px}
.badge{width:36px;height:36px;border-radius:50%;background:var(--teal);display:flex;align-items:center;justify-content:center}
.dstat b{display:block;font-size:32px;font-weight:500;line-height:34px}
.dstat span{font-size:16px;color:#333}

/* testimonials */
.tcard{top:3074px;height:230px;border-radius:16px;color:#fff;padding:34px 33px;overflow:hidden;
  background:linear-gradient(180deg,#3b4a4c,#20302f 60%,#141a19)}
.tcard h3{font-size:20px;font-weight:400;margin-bottom:12px}
.tcard p{font-size:14px;line-height:18px;color:#c9cfcd;font-weight:300;width:430px}
.tmeta{position:absolute;left:33px;right:33px;top:172px;display:flex;justify-content:space-between;font-size:13px;color:#ddd}

/* community + footer */
.footer{left:0;top:3548px;width:1200px;height:484px;background:linear-gradient(180deg,#2a2724,#1a1918)}
.community{left:40px;top:3389px;width:1120px;height:300px;border-radius:16px;background:#fff;overflow:hidden;box-shadow:0 6px 24px rgba(0,0,0,.06)}
.bubble{position:absolute;border-radius:50%}
.subscribe{left:70px;top:201px;width:308px;height:35px;border-radius:18px;background:var(--ink);display:flex;align-items:center;justify-content:space-between;padding:0 3px 0 16px;color:#fff;font-size:14px}
.subscribe span:last-child{background:#fff;color:var(--ink);border-radius:15px;height:29px;padding:0 16px;display:flex;align-items:center;font-size:13px}
.fcol{top:3773px;color:#fff}
.fcol h4{font-size:15px;font-weight:400;margin-bottom:10px}
.fcol li{list-style:none;font-size:12.5px;color:#cfcac3;font-weight:300;line-height:22px}
.soc{width:40px;height:40px;border-radius:8px;border:1px solid rgba(255,255,255,.4);display:flex;align-items:center;justify-content:center}
.soc i{width:14px;height:14px;border-radius:3px;background:#fff;display:block}
</style>
</head>
<body>

<!-- Hero -->
<header class="abs hero">
  <div class="photo" role="img" aria-label="Traveller standing on a rocky peak above misty mountains at golden hour" style="inset:0;z-index:0"></div>
  <div class="abs brand" style="left:36px;top:55px;color:#fff"><span class="brand-dot"></span>Roamwell</div>
  <nav class="abs nav">
    <a>Travel</a><a>Brimwell Vacations</a><a>Family Trips</a><a>Texas Road Trips</a><a>About</a><a>Contact</a>
  </nav>
  <div class="abs" style="left:908px;top:55px;display:flex;gap:4px">
    <a class="btn">Book your trip</a>
    <span class="arrow"><svg width="14" height="14" viewBox="0 0 14 14"><path d="M3 11L11 3M5 3h6v6" stroke="#fff" stroke-width="1.4" fill="none"/></svg></span>
  </div>
  <h1 class="abs">Let’s<br>Explore The World</h1>
  <div class="abs hero-pill" role="img" aria-label="Coastal cliffs beside calm sea"></div>
  <p class="abs hero-copy">Lorem Ipsum Dolor Sit Amet, Consectetur Adipiscing Elit, Sed Do Eiusmod Tempor Incididunt Ut Labore Et Dolore Magna Aliqua. Ut Enim Ad Minim Veniam, Quis Nostrud Exercitation Ullamco Laboris.</p>
  <div class="abs stats">
    <div class="stat"><b><svg width="16" height="16" viewBox="0 0 16 16"><path d="M8 0L9.6 6.4 16 8 9.6 9.6 8 16 6.4 9.6 0 8 6.4 6.4z" fill="#fff"/></svg>8+Yrs</b><span>Experience</span></div>
    <div class="stat"><b><svg width="16" height="16" viewBox="0 0 16 16"><path d="M8 0L9.6 6.4 16 8 9.6 9.6 8 16 6.4 9.6 0 8 6.4 6.4z" fill="#fff"/></svg>4.9/5</b><span>Average Ratings</span></div>
    <div class="stat"><b><svg width="16" height="16" viewBox="0 0 16 16"><path d="M8 0L9.6 6.4 16 8 9.6 9.6 8 16 6.4 9.6 0 8 6.4 6.4z" fill="#fff"/></svg>5M+</b><span>Happy Customers</span></div>
  </div>
  <div class="abs side"><i></i><i></i><i></i></div>
</header>

<!-- Popular destinations -->
<section>
  <div class="abs eyebrow" style="left:42px;top:843px"><svg width="16" height="16" viewBox="0 0 16 16"><path d="M8 0L9.6 6.4 16 8 9.6 9.6 8 16 6.4 9.6 0 8 6.4 6.4z" fill="var(--teal)"/></svg>EXPLORE</div>
  <h2 class="abs title" style="left:42px;top:873px">Popular Destinations</h2>
  <p class="abs lede" style="left:684px;top:848px;width:470px">Explore Our Most Loved Destinations. From Magical Theme Parks And Tropical Escapes To Breathtaking Road Trips And Cultural Adventures. Every Place Is Handpicked To Give You Unforgettable Experiences... <b>Read More.</b></p>

  <div class="photo card" role="img" aria-label="Fairytale castle under a blue sky" style="left:42px;top:970px;width:548px;height:255px;background:linear-gradient(180deg,#6fb2dc,#a8cde0 45%,#8a9ea8 100%)"><span class="abs rating">4.9 ★</span></div>
  <div class="photo card" role="img" aria-label="Family sitting together on a sunny beach by the sea" style="left:609px;top:970px;width:549px;height:255px;background:linear-gradient(180deg,#a9c3cf,#2f6f88 45%,#b49a7a 75%,#8c7358)"><span class="abs rating">4.8 ★</span></div>
  <div class="photo card" role="img" aria-label="Friends cheering in an orange open-top jeep on a country road" style="left:42px;top:1250px;width:548px;height:257px;background:linear-gradient(180deg,#b9d6ea,#d9c9a0 50%,#d88a2f 75%,#6b5a3e)"><span class="abs rating">5.0 ★</span></div>
  <div class="photo card" role="img" aria-label="Dark mountain lake with small boats" style="left:609px;top:1250px;width:549px;height:257px;background:linear-gradient(180deg,#3f4f52,#2d3e40 50%,#1f3a3c)">
    <span class="abs" style="left:0;right:0;top:117px;text-align:center;color:#fff;font-size:18px;font-weight:300">Other Destinations ↗</span>
  </div>
</section>

<!-- About -->
<section>
  <div class="photo" role="img" aria-label="Castle with blossom trees and crowds of visitors" style="left:40px;top:1590px;width:284px;height:386px;border-radius:16px;background:linear-gradient(180deg,#7eb7e0,#c7a9c9 40%,#6b6f88 70%,#4a4a52)"></div>
  <div class="photo" role="img" aria-label="Red convertible driving down an open desert highway" style="left:255px;top:1712px;width:311px;height:386px;border-radius:16px;border:4px solid #fff;background:linear-gradient(180deg,#dfe3e2,#c7bda7 45%,#8a8170 70%,#5b5249)">
    <span class="abs" style="left:128px;top:171px;width:52px;height:52px;border-radius:50%;background:rgba(255,255,255,.7);display:flex;align-items:center;justify-content:center"><svg width="14" height="16" viewBox="0 0 14 16"><path d="M2 1l11 7-11 7z" fill="var(--ink)"/></svg></span>
  </div>
  <div class="abs eyebrow" style="left:599px;top:1647px"><svg width="16" height="16" viewBox="0 0 16 16"><path d="M8 0L9.6 6.4 16 8 9.6 9.6 8 16 6.4 9.6 0 8 6.4 6.4z" fill="var(--teal)"/></svg>CRAFTED FOR WONDER</div>
  <h2 class="abs title" style="left:599px;top:1678px">Know More About Us</h2>
  <div class="abs" style="left:599px;top:1735px;width:560px">
    <p class="para">Lorem Ipsum Dolor Sit Amet, Consectetur Adipiscing Elit, Sed Do Eiusmod Tempor Incididunt Ut Labore Et Dolore Magna Aliqua. Ut Enim Ad Minim Veniam, Quis Nostrud Exercitation Ullamco Laboris.UllamcullamcLorem Ipsum Dolor Sit Amet.</p>
    <p class="para">Lorem Ipsum Dolor Sit Amet, Consectetur Adipiscing Elit, Sed Do Eiusmod Tempor Incididunt Ut Labore Et Dolore Magna Aliqua. Ut Enim Ad Minim Veniam, Quis Nostrud Exercitation Ullamco Laboris.UllamcLorem Ipsum Dolor Sit Amet, Consectetur Adipiscing Elit, Sed</p>
    <p class="para">Lorem Ipsum Dolor Sit Amet, Consectetur Adipiscing Elit, Sed Do Eiusmod Tempor Incididunt Ut Labore Et Dolore Magna Aliqua. Ut Enim Ad Minim Veniam, Quis Nostrud Exercitation Ullamco Laboris.UllamcLorem Ipsum Dolor.</p>
  </div>
  <div class="abs" style="left:599px;top:2006px;display:flex;gap:4px">
    <a class="btn" style="height:40px">Book your trip</a>
    <span class="arrow"><svg width="14" height="14" viewBox="0 0 14 14"><path d="M3 11L11 3M5 3h6v6" stroke="#fff" stroke-width="1.4" fill="none"/></svg></span>
  </div>
</section>

<!-- What makes us different -->
<section>
  <div class="abs eyebrow" style="left:40px;top:2192px"><svg width="16" height="16" viewBox="0 0 16 16"><path d="M8 0L9.6 6.4 16 8 9.6 9.6 8 16 6.4 9.6 0 8 6.4 6.4z" fill="var(--teal)"/></svg>WHY CHOOSE US</div>
  <h2 class="abs title" style="left:40px;top:2221px">What Makes Us Different</h2>
  <p class="abs lede" style="left:682px;top:2198px;width:478px">We Create Unforgettable Travel Experiences Designed Around Comfort, Wonder, And Adventure. From Magical Destinations To Seamless Planning, Every Journey Is Carefully Crafted To Help You Explore The World With Ease... <b>Read More</b></p>

  <div class="photo card" role="img" aria-label="Travellers reading a map together on stone steps" style="left:39px;top:2317px;width:549px;height:257px;background:linear-gradient(180deg,#9a8f80,#c2b49c 50%,#6e6256)"></div>
  <div class="photo card" role="img" aria-label="Hiker on a summit above a sea of clouds" style="left:605px;top:2317px;width:550px;height:257px;background:linear-gradient(180deg,#1d4f8f,#5d8fc0 45%,#e4eef5 70%,#5a4b40)"></div>
  <div class="photo card" role="img" aria-label="Silhouetted hiker against an orange sunset over hills" style="left:39px;top:2599px;width:549px;height:256px;background:linear-gradient(180deg,#f7efe6,#f2c592 45%,#c9772f 75%,#3d2414)"></div>
  <div class="photo card" role="img" aria-label="Group of friends hiking through green grassland" style="left:605px;top:2599px;width:550px;height:256px;background:linear-gradient(180deg,#dfe6e2,#8fa883 45%,#4e6a3c 75%,#3a4630)"></div>

  <div class="abs statbar">
    <div class="dstat" style="left:40px"><span class="badge"><svg width="16" height="18" viewBox="0 0 16 18"><circle cx="8" cy="7" r="5" fill="none" stroke="#fff" stroke-width="1.6"/><path d="M5 11l-1 6 4-2 4 2-1-6" fill="none" stroke="#fff" stroke-width="1.6"/></svg></span><div><b>10k+</b><span>Happy Customers</span></div></div>
    <div class="dstat" style="left:287px"><span class="badge"><svg width="16" height="18" viewBox="0 0 16 18"><circle cx="8" cy="7" r="5" fill="none" stroke="#fff" stroke-width="1.6"/><path d="M5 11l-1 6 4-2 4 2-1-6" fill="none" stroke="#fff" stroke-width="1.6"/></svg></span><div><b>100K+</b><span>5 Star Ratings</span></div></div>
    <div class="dstat" style="left:532px"><span class="badge"><svg width="16" height="18" viewBox="0 0 16 18"><circle cx="8" cy="7" r="5" fill="none" stroke="#fff" stroke-width="1.6"/><path d="M5 11l-1 6 4-2 4 2-1-6" fill="none" stroke="#fff" stroke-width="1.6"/></svg></span><div><b>10yrs+</b><span>Experience</span></div></div>
    <div class="dstat" style="left:780px"><span class="badge"><svg width="16" height="18" viewBox="0 0 16 18"><circle cx="8" cy="7" r="5" fill="none" stroke="#fff" stroke-width="1.6"/><path d="M5 11l-1 6 4-2 4 2-1-6" fill="none" stroke="#fff" stroke-width="1.6"/></svg></span><div><b>800+</b><span>Trips Done Wroldwide</span></div></div>
  </div>
</section>

<!-- Testimonials -->
<section>
  <div class="abs eyebrow" style="left:40px;top:2948px"><svg width="16" height="16" viewBox="0 0 16 16"><path d="M8 0L9.6 6.4 16 8 9.6 9.6 8 16 6.4 9.6 0 8 6.4 6.4z" fill="var(--teal)"/></svg>TESTIMONIALS</div>
  <h2 class="abs title" style="left:40px;top:2977px">What Our Clients Say</h2>
  <div class="abs" style="left:979px;top:2963px;display:flex;gap:4px">
    <a class="btn" style="height:40px">Book your trip</a>
    <span class="arrow"><svg width="14" height="14" viewBox="0 0 14 14"><path d="M3 11L11 3M5 3h6v6" stroke="#fff" stroke-width="1.4" fill="none"/></svg></span>
  </div>
  <div style="position:absolute;left:0;top:0;width:1160px;height:4032px;overflow:hidden">
    <article class="abs tcard" role="img" aria-label="Review card over a dark mountain lake scene" style="left:39px;width:493px">
      <h3>Excellent Trip</h3>
      <p>lorem ipsum dolor sit amet, consectetur adipiscing elit, sed do eiusmod tempor incididunt ut labore et lorem ipsum dolor sit amet, consectetur adipiscing elit, sed do eiusmod tempor incididunt ut labore et</p>
      <div class="tmeta"><span>Jhon Doe &nbsp;|&nbsp; 08.10.26</span><span>★ &nbsp; 5.0</span></div>
    </article>
    <article class="abs tcard" role="img" aria-label="Review card over a dark mountain lake scene" style="left:554px;width:491px">
      <h3>Excellent Trip</h3>
      <p>lorem ipsum dolor sit amet, consectetur adipiscing elit, sed do eiusmod tempor incididunt ut labore et lorem ipsum dolor sit amet, consectetur adipiscing elit, sed do eiusmod tempor incididunt ut labore et</p>
      <div class="tmeta"><span>Jhon Doe &nbsp;|&nbsp; 08.10.26</span><span>★ &nbsp; 5.0</span></div>
    </article>
    <article class="abs tcard" role="img" aria-label="Review card over a dark mountain lake scene" style="left:1067px;width:491px">
      <h3>Excellent Trip</h3>
      <p>lorem ipsum dolor sit amet, consectetur adipiscing elit, sed do eiusmod tempor incididunt ut labore et lorem ipsum dolor sit amet, consectetur adipiscing elit, sed do eiusmod tempor incididunt ut labore et</p>
      <div class="tmeta"><span>Jhon Doe &nbsp;|&nbsp; 08.10.26</span><span>★ &nbsp; 5.0</span></div>
    </article>
  </div>
</section>

<!-- Footer -->
<footer class="abs footer" role="img" aria-label="Dusky coastal town at evening, dimmed behind the footer"></footer>

<section class="abs community">
  <h2 class="abs title" style="left:70px;top:65px">Join the Community</h2>
  <p class="abs lede" style="left:70px;top:122px;width:420px;color:#777">Join our community and be the first to receive exclusive offers, expert travel tips, and early access to exciting new product launches—delivered straight to your inbox.</p>
  <div class="abs subscribe"><span>Enter email</span><span>Subscribe</span></div>
  <div class="bubble" role="img" aria-label="Traveller standing on a rock by turquoise water" style="left:598px;top:-1px;width:140px;height:140px;background:linear-gradient(180deg,#2b8fa3,#5ab4bf 60%,#8b7a66)"></div>
  <div class="bubble" role="img" aria-label="Hands holding passports in a city street" style="left:852px;top:-17px;width:162px;height:162px;background:linear-gradient(180deg,#c7c2bb,#8e8479 55%,#3d3a3a)"></div>
  <div class="bubble" role="img" aria-label="Person leaping on a beach under a blue sky" style="left:1044px;top:31px;width:132px;height:132px;background:linear-gradient(180deg,#7fb6dd,#d8e7ef 60%,#c3a586)"></div>
  <div class="bubble" role="img" aria-label="Couple sitting on a grassy hillside" style="left:744px;top:116px;width:100px;height:100px;background:linear-gradient(180deg,#e6e6da,#9bb27e 55%,#6b7d4c)"></div>
  <div class="bubble" role="img" aria-label="Passports held in front of old buildings" style="left:540px;top:173px;width:166px;height:166px;background:linear-gradient(180deg,#b7b1aa,#7a6f66 55%,#2d2b2c)"></div>
  <div class="bubble" role="img" aria-label="Traveller overlooking a rocky coastline" style="left:965px;top:166px;width:150px;height:150px;background:linear-gradient(180deg,#d8c6b4,#4d5e6b 55%,#2a3138)"></div>
</section>

<div class="abs brand" style="left:55px;top:3821px;color:#fff;font-size:26px"><span class="brand-dot" style="width:44px;height:44px"></span>Roamwell</div>

<div class="abs fcol" style="left:357px"><h4>Explore</h4><ul><li>What We Offer</li><li>Blog &amp; Insights</li><li>Resources</li><li>FAQs</li></ul></div>
<div class="abs fcol" style="left:548px"><h4>Company</h4><ul><li>Home</li><li>About Us</li><li>Contact Us</li><li>Testimonials</li></ul></div>
<div class="abs fcol" style="left:740px"><h4>Legal Links</h4><ul><li>Privacy Policy</li><li>Cookie Policy</li><li>Disclaimer</li><li>Copyright</li></ul></div>
<div class="abs fcol" style="left:932px"><h4>Social</h4>
  <div style="display:flex;gap:20px;margin-top:18px"><span class="soc"><i></i></span><span class="soc"><i></i></span><span class="soc"><i></i></span><span class="soc"><i></i></span></div>
</div>

<div class="abs" style="left:40px;top:3953px;width:1120px;height:1px;background:rgba(255,255,255,.15)"></div>
<p class="abs" style="left:43px;top:3980px;color:#cfcac3;font-size:12.5px;font-weight:300">Copyright © 2025 roamwell travel co. All Rights Reserved.</p>
<p class="abs" style="left:938px;top:3980px;color:#cfcac3;font-size:12.5px;font-weight:300;display:flex;gap:20px"><span>Teams &amp; Conditions</span><span>Privacy Policy</span></p>

</body>
</html>
```